Brightfen Business Card Redesign & Logo Update

We need to update our business cards to something more modern and fresh. Brightfen can provide the current color schemes and old design examples, but welcome creativity in helping us with this redesign. PLEASE NOTE that we no longer utilize the "tree" and/or "leaf" imagery in our branding. If able would apprecaite an update on the quality of our "words only" logo in Ai. / PNG formats too.

Target Market(s)

Investors, landowners, corporate partners, contractors

Industry/Entity Type

Environmental Restoration & Conservation

Contact Information for Business Card

Logo, persons name, title, mailing address, phone and email, website url

Font styles to use
Other font styles liked:
• Merriweather

Requirements
Nice to have
• Logo, persons name, title, mailing address, phone and email, website url, but open to ideams
Should not have
• No all back backgrounds

```html
<!DOCTYPE html>
<html lang="en">
<head>
<meta charset="utf-8">
<title>Brightfen Business Card</title>
<link href="https://fonts.googleapis.com/css2?family=Montserrat:wght@500;700;800&display=swap" rel="stylesheet">
<style>
  :root {
    --backdrop: #8e8e8e;
    --card: #ffffff;
    --green: #167d43;
    --orange: #ee8022;
    --ink: #1c1c1c;
    --radius: 28px;
  }
  * { margin: 0; padding: 0; box-sizing: border-box; }
  html, body {
    width: 1160px;
    height: 1200px;
    overflow: hidden;
    background: var(--backdrop);
    font-family: "Montserrat", Arial, sans-serif;
    color: var(--ink);
  }
  .canvas { position: relative; width: 1160px; height: 1200px; }
  .card {
    position: absolute;
    left: 199px;
    width: 777px;
    height: 442px;
    background: var(--card);
    border-radius: var(--radius);
    overflow: hidden;
  }
  .card--front { top: 104px; }
  .card--back { top: 634px; }

  .person { position: absolute; left: 36px; top: 66px; }
  .person__name {
    font-weight: 800;
    font-size: 25px;
    letter-spacing: 0.2px;
    color: var(--orange);
  }
  .person__name .first { color: var(--green); }
  .person__title { font-weight: 500; font-size: 19px; margin-top: 4px; }

  .brand-name {
    font-weight: 800;
    color: var(--green);
    letter-spacing: 1px;
    line-height: 1;
  }
  .card--front .brand-name {
    position: absolute;
    right: 40px;
    top: 60px;
    font-size: 50px;
  }
  .card--back .brand-name {
    position: absolute;
    left: 0; right: 0;
    top: 180px;
    text-align: center;
    font-size: 82px;
  }

  .contact { position: absolute; left: 36px; top: 266px; list-style: none; }
  .contact__item {
    display: flex;
    align-items: center;
    height: 34.5px;
    font-weight: 500;
    font-size: 21px;
  }
  .contact__icon { width: 27px; height: 27px; margin-right: 14px; flex: none; }

  .address {
    position: absolute;
    right: 38px;
    top: 309px;
    text-align: right;
    font-style: normal;
    font-weight: 500;
    font-size: 19px;
    line-height: 28px;
  }

  .footer-rule {
    position: absolute;
    left: 0; right: 0;
    top: 400px;
    height: 6px;
    background: var(--orange);
  }
  .footer-band {
    position: absolute;
    left: 0; right: 0;
    bottom: 0;
    height: 30px;
    background: var(--green);
  }
</style>
</head>
<body>
<main class="canvas">

  <section class="card card--front">
    <div class="person">
      <p class="person__name"><span class="first">DANA</span> HOLLIS</p>
      <p class="person__title">Managing Director</p>
    </div>

    <p class="brand-name">BRIGHTFEN</p>

    <ul class="contact">
      <li class="contact__item">
        <svg class="contact__icon" viewBox="0 0 28 28" aria-hidden="true">
          <circle cx="14" cy="14" r="14" fill="var(--orange)"/>
          <path d="M7 12c0-3 3-4 7-4s7 1 7 4l-3 1-1-2h-6l-1 2z" fill="#fff"/>
          <rect x="9" y="14" width="10" height="6" rx="1.5" fill="#fff"/>
        </svg>
        555-014-2290
      </li>
      <li class="contact__item">
        <svg class="contact__icon" viewBox="0 0 28 28" aria-hidden="true">
          <circle cx="14" cy="14" r="14" fill="var(--orange)"/>
          <rect x="7" y="9" width="14" height="10" rx="1" fill="none" stroke="#fff" stroke-width="1.6"/>
          <path d="M7.5 9.5 14 15l6.5-5.5" fill="none" stroke="#fff" stroke-width="1.6"/>
        </svg>
        info@brightfen.com
      </li>
      <li class="contact__item">
        <svg class="contact__icon" viewBox="0 0 28 28" aria-hidden="true">
          <circle cx="14" cy="14" r="14" fill="var(--orange)"/>
          <circle cx="14" cy="14" r="7" fill="none" stroke="#fff" stroke-width="1.6"/>
          <path d="M7 14h14M14 7c-3 3-3 11 0 14M14 7c3 3 3 11 0 14" fill="none" stroke="#fff" stroke-width="1.2"/>
        </svg>
        www.brightfen.com
      </li>
    </ul>

    <address class="address">
      42-07 Alder Lane 14<br>
      Fairhaven, NY 11520
    </address>

    <div class="footer-rule"></div>
    <div class="footer-band"></div>
  </section>

  <section class="card card--back">
    <p class="brand-name">BRIGHTFEN</p>
  </section>

</main>
</body>
</html>
```